TLK Electricial Contracting Services

Hi guys, after a design for my small electrical company, have logo design files to be incorporated into the layout, the basic concept is electrical contracting services for residential, commercial, industrial & data services, image is clean clear and strong,

Card format is to have a nice clean logo on front,with maybe the Residential – commercial – industrial - data, followed with licensed & insured, followed by contact details on backside of the card.

Target Market(s)

Residential, commercial, industrial sectors.

Industry/Entity Type

Electrical

Contact Information for Business Card

TLK logo,
Residential – commercial – industrial - data
REC: 61307
Email: tlk@vornamail.net.au
Phone: 0487 352 019

Requirements
Must have
• Clean & strong design.
Nice to have
• If possible, I would like the logo colours inverted so the text is orange and the background is black on the front of the card, then the backside of the card be the reverse colour
Should not have
• No Sparks, lightning bolts,

```html
<!DOCTYPE html>
<html lang="en">
<head>
<meta charset="utf-8">
<title>TLK Electrical Contracting Services – Business Card</title>
<link rel="stylesheet" href="https://fonts.googleapis.com/css2?family=Archivo:wght@400;500;600;700&display=swap">
<style>
  :root {
    --backdrop: #efefef;
    --orange: #ef8a3a;
    --charcoal: #232323;
    --ink: #1c1c1c;
    --card-w: 500px;
    --card-h: 286px;
  }
  * { box-sizing: border-box; margin: 0; padding: 0; }
  html, body {
    width: 1200px;
    height: 800px;
    overflow: hidden;
    background: var(--backdrop);
    font-family: "Archivo", Arial, sans-serif;
  }
  .canvas {
    position: relative;
    width: 1200px;
    height: 800px;
  }
  .card {
    position: absolute;
    top: 257px;
    width: var(--card-w);
    height: var(--card-h);
    box-shadow: 0 2px 6px rgba(0,0,0,0.12);
  }
  /* Contact side */
  .card--contact {
    left: 75px;
    background: var(--orange);
    color: var(--ink);
  }
  .card--contact .brand {
    position: absolute;
    top: 30px;
    right: 36px;
    font-size: 40px;
    font-weight: 700;
    letter-spacing: -1px;
    color: var(--ink);
    line-height: 1;
  }
  .licence {
    position: absolute;
    top: 92px;
    left: 40px;
    font-size: 10px;
    font-weight: 500;
    letter-spacing: 0.5px;
  }
  .name {
    position: absolute;
    left: 40px;
    top: 160px;
    font-size: 25px;
    font-weight: 700;
    line-height: 1;
  }
  .rule {
    position: absolute;
    left: 40px;
    top: 190px;
    width: 422px;
    height: 2px;
    background: var(--ink);
  }
  .role {
    position: absolute;
    left: 40px;
    top: 197px;
    font-size: 10px;
    font-weight: 500;
  }
  .contact-line {
    position: absolute;
    display: flex;
    align-items: center;
    gap: 8px;
    font-weight: 600;
  }
  .contact-line svg { width: 14px; height: 14px; fill: var(--ink); }
  .contact-line--phone { left: 40px; top: 218px; font-size: 19px; }
  .contact-line--email { right: 38px; top: 202px; font-size: 17px; }

  /* Brand side */
  .card--brand {
    left: 625px;
    background: var(--charcoal);
    color: var(--orange);
  }
  .card--brand .lockup {
    position: absolute;
    left: 48px;
    top: 150px;
    display: flex;
    align-items: center;
    gap: 20px;
  }
  .card--brand .brand {
    font-size: 44px;
    font-weight: 700;
    letter-spacing: -1px;
    line-height: 1;
  }
  .divider {
    width: 2px;
    height: 66px;
    background: var(--orange);
  }
  .services {
    font-size: 21px;
    font-weight: 600;
    line-height: 1.2;
  }
</style>
</head>
<body>
<main class="canvas">
  <section class="card card--contact" aria-label="Card back with contact details">
    <div class="brand">TLK</div>
    <p class="licence">REC. 61307</p>
    <h1 class="name">Tomas Lakin</h1>
    <div class="rule"></div>
    <p class="role">Electrical</p>
    <p class="contact-line contact-line--phone">
      <svg viewBox="0 0 24 24" aria-hidden="true"><path d="M6.6 10.8a15.1 15.1 0 0 0 6.6 6.6l2.2-2.2a1 1 0 0 1 1-.25 11.4 11.4 0 0 0 3.6.57 1 1 0 0 1 1 1V20a1 1 0 0 1-1 1A17 17 0 0 1 3 4a1 1 0 0 1 1-1h3.5a1 1 0 0 1 1 1c0 1.25.2 2.45.57 3.57a1 1 0 0 1-.25 1z"/></svg>
      0487 352 019
    </p>
    <p class="contact-line contact-line--email">
      <svg viewBox="0 0 24 24" aria-hidden="true"><path d="M2 5h20v14H2zm2 2v.4l8 5.2 8-5.2V7zm0 2.8V17h16V9.8l-8 5.2z"/></svg>
      tlk@vornamail.net.au
    </p>
  </section>

  <section class="card card--brand" aria-label="Card front with logo and services">
    <div class="lockup">
      <div class="brand">TLK</div>
      <div class="divider"></div>
      <p class="services">Residential, Commercial<br>Industrial &amp; Data Services</p>
    </div>
  </section>
</main>
</body>
</html>
```